Boutique custom software development company needs new business card

Our nearly 20 year old custom software development company would like to better include the fact that we are now providing Bitcoin services. These new services are B2B include education (how to acquire and securely hold Bitcoin) and integrating Bitcoin payments into existing ecommerce sites or other existing systems. Please keep the card clean and simple. Attached is our current design and some other files. vextorial.com

Target Market(s)

businesses owners interested in long term relationship

Industry/Entity Type

Custom software development and Bitcoin

Contact Information for Business Card

Dale Parker, dale@vextorial.com, vextorial.com, (888) 555-VXTRL

Font styles to use
Other font styles liked:
• monospace

Requirements
Must have
• double-sided
Nice to have
• clean and simple
Should not have
• physical address

```html
<!DOCTYPE html>
<html lang="en">
<head>
<meta charset="utf-8">
<title>Vextorial – Business Card</title>
<link href="https://fonts.googleapis.com/css2?family=Arimo:wght@400;700&family=Lato:wght@400;700&display=swap" rel="stylesheet">
<style>
  :root {
    --backdrop: #9a9a9a;
    --paper: #dfe5ee;
    --brand-blue: #3a73bb;
    --brand-orange: #ef7d22;
    --ink-grey: #555a60;
    --white: #ffffff;
  }
  html, body {
    margin: 0;
    padding: 0;
    width: 1200px;
    height: 952px;
    overflow: hidden;
    background: var(--backdrop);
  }
  .canvas {
    position: relative;
    width: 1200px;
    height: 952px;
  }
  .card {
    position: absolute;
    left: 320px;
    width: 560px;
    height: 320px;
    box-shadow: 0 14px 30px rgba(0,0,0,0.25);
    box-sizing: border-box;
    overflow: hidden;
  }
  .card--front { top: 126px; background: var(--paper); }
  .card--back  { top: 506px; background: var(--brand-blue); }

  /* Front: contact block */
  .contact {
    position: absolute;
    left: 44px;
    top: 92px;
    font-family: "Arimo", Arial, sans-serif;
  }
  .contact__name {
    margin: 0;
    font-size: 22px;
    font-weight: 700;
    letter-spacing: 0.5px;
    line-height: 1;
  }
  .contact__first { color: var(--brand-orange); }
  .contact__last  { color: var(--brand-blue); }
  .contact__role {
    margin: 4px 0 18px;
    font-size: 14px;
    color: var(--ink-grey);
  }
  .contact__list {
    list-style: none;
    margin: 0;
    padding: 0;
  }
  .contact__item {
    display: flex;
    align-items: center;
    gap: 7px;
    font-size: 14px;
    color: var(--ink-grey);
    margin-bottom: 8px;
  }
  .contact__icon { width: 11px; height: 11px; fill: var(--brand-blue); }

  .divider {
    position: absolute;
    left: 278px;
    top: 96px;
    width: 2px;
    height: 128px;
  }

  /* Brand lockup */
  .brand {
    position: absolute;
    font-family: "Arimo", Arial, sans-serif;
  }
  .brand__name {
    margin: 0;
    font-weight: 700;
    line-height: 1;
    letter-spacing: -0.5px;
  }
  .brand__tagline {
    margin: 4px 0 0;
    font-family: "Lato", Arial, sans-serif;
    font-weight: 400;
    white-space: nowrap;
  }
  .brand__services {
    margin: 6px 0 0;
    font-family: "Lato", Arial, sans-serif;
    font-weight: 700;
    color: var(--brand-orange);
    white-space: nowrap;
  }
  .card--front .brand { left: 312px; top: 118px; }
  .card--front .brand__name { font-size: 46px; color: var(--brand-blue); }
  .card--front .brand__tagline { font-size: 15px; color: var(--brand-blue); }
  .card--front .brand__services { font-size: 13px; }

  .card--back .brand { left: 40px; top: 94px; }
  .card--back .brand__name { font-size: 74px; color: var(--white); }
  .card--back .brand__tagline { font-size: 22px; color: var(--white); }
  .card--back .brand__services { font-size: 18px; }
</style>
</head>
<body>
<main class="canvas">

  <section class="card card--front" aria-label="Card front">
    <div class="contact">
      <h1 class="contact__name"><span class="contact__first">DALE</span> <span class="contact__last">PARKER</span></h1>
      <p class="contact__role">Owner</p>
      <ul class="contact__list">
        <li class="contact__item">
          <svg class="contact__icon" viewBox="0 0 12 12" aria-hidden="true"><path d="M2.5 0.5l2 2.5-1.2 1.3c0.7 1.5 2 2.8 3.4 3.4l1.3-1.2 2.5 2-1.2 2.2C5 10.5 1.5 7 0.3 1.7z"/></svg>
          (888) 555-VXTRL
        </li>
        <li class="contact__item">
          <svg class="contact__icon" viewBox="0 0 12 12" aria-hidden="true"><path d="M0 2h12v8H0z M0.8 2.6L6 6.6l5.2-4z" fill-rule="evenodd"/></svg>
          dale@vextorial.com
        </li>
        <li class="contact__item">
          <svg class="contact__icon" viewBox="0 0 12 12" aria-hidden="true"><circle cx="6" cy="6" r="5.5"/><path d="M0.5 6h11M6 0.5c-2 2.5-2 8.5 0 11M6 0.5c2 2.5 2 8.5 0 11" stroke="#dfe5ee" stroke-width="0.8" fill="none"/></svg>
          www.vextorial.com
        </li>
      </ul>
    </div>

    <svg class="divider" viewBox="0 0 2 128" aria-hidden="true">
      <rect x="0" y="0" width="2" height="46" fill="#3a73bb"/>
      <rect x="0" y="46" width="2" height="36" fill="#ef7d22"/>
      <rect x="0" y="82" width="2" height="46" fill="#3a73bb"/>
    </svg>

    <div class="brand">
      <p class="brand__name">Vextorial</p>
      <p class="brand__tagline">developer of custom applications</p>
      <p class="brand__services">+ Bitcoin services for business</p>
    </div>
  </section>

  <section class="card card--back" aria-label="Card back">
    <div class="brand">
      <p class="brand__name">Vextorial</p>
      <p class="brand__tagline">developer of custom applications</p>
      <p class="brand__services">Bitcoin education &amp; payment integration</p>
    </div>
  </section>

</main>
</body>
</html>
```